brovlanepass.net

Develop a website for brolanepass.net will be a site to sell tickets for concerts, shows, shows, theaters and others. I need a web design easy view, very easy to use and accumulate events by date. The aim is to develop the site was connected to a complex system that is already developed. (Important this page to a robust system was connected via links the idea is to develop only the front view)
Updates

Reason: I need more designs yet we have not made the decision

Target Market(s)

millennials, adults, who want to enjoy concerts and shows

Industry/Entity Type

Event

Number of Pages Required

5+ page

Colors
1b1b1b
aaaaaa
ffffff

Requirements
Must have
• Easy Vista, accumulation of upcoming events, past events. The tabs should have are: 1 Start: In this part of upcoming events occur. You could put a banner on the top and down the events by date. 2. How to order: page with instructions on how to purchase tickets 3. About Us: The company history 4. Contact: Phones and template for contact by mail 5. Our policies: shopping 6. Notice Privacy: Privacy Notice Copoy 7. Centers Sale: physical places where they can purchase tickets Promoters 8. access: Link to a template
Nice to have
• as you can see p www.quimbarostage.net or farunda.net or farunda.org or gallowmerk.net (important this page to a robust system was connected via links the idea is to develop only the front view)
Should not have
• Many things Tangled

```html
<!DOCTYPE html>
<html lang="en">
<head>
<meta charset="utf-8">
<title>Brovlane Pass</title>
<link href="https://fonts.googleapis.com/css2?family=Mulish:wght@400;600;700&display=swap" rel="stylesheet">
<style>
:root{
  --ink:#1b1b1b;
  --ink-soft:#444444;
  --grey:#aaaaaa;
  --white:#ffffff;
  --badge:rgba(40,40,40,.82);
  --text:#555555;
}
*{box-sizing:border-box;margin:0;padding:0}
html,body{width:1200px;height:2287px;overflow:hidden;background:var(--white);font-family:"Mulish",Arial,sans-serif;color:var(--ink)}
.page{position:relative;width:1200px;height:2287px}

.site-header{position:absolute;left:0;top:0;width:1200px;height:96px;background:var(--ink);color:var(--white);z-index:3}
.brand{position:absolute;left:99px;top:36px;font-size:25px;font-weight:700;letter-spacing:.5px}
.contact-line{position:absolute;right:99px;top:18px;font-size:13px;display:flex;gap:26px}
.contact-line span{display:flex;align-items:center;gap:9px}
.main-nav{position:absolute;right:99px;top:60px;display:flex;gap:30px;font-size:14px}

.hero{position:absolute;left:0;top:96px;width:1200px;height:589px}
.hero-photo{position:absolute;inset:0}
.hero-title{position:absolute;left:0;width:1200px;top:242px;text-align:center;color:var(--white);font-size:40px;font-weight:700;letter-spacing:.3px;line-height:1.2}
.hero-button{position:absolute;left:425px;top:335px;width:350px;height:44px;border:2px solid var(--white);color:var(--white);font-size:22px;display:flex;align-items:center;justify-content:center}
.slider-dots{position:absolute;left:564px;top:528px;display:flex;gap:11px}
.slider-dots i{width:14px;height:14px;border:2px solid var(--white);border-radius:50%}
.slider-dots i.active{background:radial-gradient(circle,var(--white) 2.5px,transparent 3px)}

.welcome{position:absolute;left:0;top:756px;width:1200px;text-align:center}
.welcome h1{font-size:32px;font-weight:600;color:var(--ink-soft)}
.welcome p{width:856px;margin:30px auto 0;font-size:11.5px;line-height:21px;color:var(--text)}
.read-more{position:absolute;left:532px;top:185px;width:136px;height:43px;background:var(--ink);color:var(--white);font-size:19px;display:flex;align-items:center;justify-content:center}

.events-title{position:absolute;left:99px;top:1061px;font-size:27px;font-weight:600;color:var(--ink-soft)}
.event-arrows{position:absolute;left:1046px;top:1064px;display:flex;gap:9px}
.event-arrows span{width:22px;height:22px;background:#555;display:flex;align-items:center;justify-content:center}
.event-tabs{position:absolute;left:0;width:1200px;top:1133px;display:flex;justify-content:center;gap:38px;font-size:18px;color:#666}
.event-tabs .current{color:var(--ink);font-weight:700}

.event-card{position:absolute;width:270px;height:368px;overflow:hidden}
.poster{position:absolute;inset:0}
.event-date{position:absolute;left:0;bottom:0;width:72px;height:72px;background:var(--badge);color:var(--white);padding:8px 0 0 16px;line-height:1}
.event-date b{display:block;font-size:30px;font-weight:700}
.event-date small{display:block;font-size:19px;font-weight:700;margin-top:3px}
.card-actions{position:absolute;left:0;top:158px;width:270px;display:flex;justify-content:center;gap:30px;color:var(--white);font-size:17px;font-weight:700;text-align:center}
.card-actions div{display:flex;flex-direction:column;align-items:center;gap:8px}

.site-footer{position:absolute;left:0;top:2054px;width:1200px;height:233px;background:var(--ink);color:var(--white)}
.social{position:absolute;left:503px;top:29px;display:flex;gap:12px}
.social span{width:32px;height:32px;border:1px solid #777;background:#2e2e2e}
.apps{position:absolute;left:473px;top:89px;display:flex;gap:12px}
.apps span{width:120px;height:36px;background:#000;border:1px solid #555;border-radius:4px;display:flex;align-items:center;gap:8px;padding-left:12px;font-size:14px;font-weight:600}
.apps span i{width:12px;height:12px;background:var(--white)}
.footer-links{position:absolute;left:0;top:148px;width:1200px;display:flex;justify-content:center;gap:28px;font-size:14px;font-weight:600}
.footer-rule{position:absolute;left:99px;top:189px;width:982px;height:1px;background:#3a3a3a}
.copyright{position:absolute;left:0;top:204px;width:1200px;text-align:center;font-size:12px;font-weight:600}
</style>
</head>
<body>
<div class="page">

<header class="site-header">
  <div class="brand">BROVLANE PASS</div>
  <div class="contact-line">
    <span><svg width="12" height="12" viewBox="0 0 12 12"><path d="M2 1l2.5 0 1 3-1.5 1c.7 1.4 1.6 2.3 3 3l1-1.5 3 1V11c-5 0-9-4-9-10z" fill="#fff"/></svg>555 0142 7788</span>
    <span><svg width="13" height="10" viewBox="0 0 13 10"><rect width="13" height="10" fill="#fff"/><path d="M0 0l6.5 5L13 0" stroke="#1b1b1b" fill="none"/></svg>info@brovlanepass.net</span>
  </div>
  <nav class="main-nav">
    <span>Home</span><span>How to Order</span><span>About Us</span><span>Contact Us</span><span>Policies</span><span>Privacy</span><span>Center Sale</span><span>Access</span>
  </nav>
</header>

<section class="hero">
  <svg class="hero-photo" width="1200" height="589" viewBox="0 0 1200 589" role="img" aria-label="Concert crowd with raised hands under warm stage lights">
    <defs>
      <radialGradient id="stageGlow" cx="0.55" cy="0.2" r="0.8">
        <stop offset="0" stop-color="#b89a92"/>
        <stop offset="0.45" stop-color="#6b4a3c"/>
        <stop offset="1" stop-color="#24150f"/>
      </radialGradient>
    </defs>
    <polygon points="0,0 1200,0 1200,493 600,589 0,493" fill="url(#stageGlow)"/>
  </svg>
  <h2 class="hero-title">MAKE YOUR SPECIAL DAY WITH US</h2>
  <div class="hero-button">Click Here To Book Ticket</div>
  <div class="slider-dots"><i class="active"></i><i></i><i></i></div>
</section>

<section class="welcome">
  <h1>Welcome To Brovlane Pass</h1>
  <p>Lorem Ipsum has been the industry's standard dummy text ever since the 1500s, when an unknown printer took a galley of type and scrambled it to make a type specimen book. It has survived not only five centuries, but also the leap into electronic typesetting, remaining essentially unchanged. It was popularised in the 1960s with the release of Quillmark sheets containing Lorem Ipsum passages, and more recently with desktop publishing software like Pagewright Studio including versions of Lorem Ipsum.</p>
  <div class="read-more">Read More</div>
</section>

<h2 class="events-title">UPCOMING EVENTS</h2>
<div class="event-arrows">
  <span><svg width="8" height="10"><path d="M7 0v10L0 5z" fill="#fff"/></svg></span>
  <span><svg width="8" height="10"><path d="M1 0v10l7-5z" fill="#fff"/></svg></span>
</div>
<nav class="event-tabs">
  <span class="current">Concerts</span><span>Shows</span><span>Theaters</span><span>Music</span><span>Sports</span><span>Arts</span>
</nav>

<article class="event-card" style="left:131px;top:1200px">
  <div class="poster" role="img" aria-label="Concert poster for a regional band at the coliseum" style="background:linear-gradient(#2a3a33,#152a22 60%,#10201a)"></div>
  <div class="poster" style="background:rgba(0,0,0,.35)"></div>
  <div class="card-actions">
    <div><svg width="18" height="16" viewBox="0 0 18 16"><path d="M0 1h3l2 9h10l2-7H5" stroke="#fff" stroke-width="2" fill="none"/><circle cx="6" cy="14" r="1.6" fill="#fff"/><circle cx="14" cy="14" r="1.6" fill="#fff"/></svg>BUY NOW</div>
    <div><svg width="16" height="16" viewBox="0 0 16 16"><circle cx="8" cy="8" r="8" fill="#fff"/><rect x="7" y="7" width="2" height="6" fill="#000"/><circle cx="8" cy="4.3" r="1.2" fill="#000"/></svg>READ MORE</div>
  </div>
  <div class="event-date"><b>16</b><small>FEB</small></div>
</article>

<article class="event-card" style="left:465px;top:1200px">
  <div class="poster" role="img" aria-label="Bullfighting festival poster with arena" style="background:linear-gradient(#f1e7de,#e6a08e 45%,#f0ece4)"></div>
  <div class="event-date"><b>19</b><small>FEB</small></div>
</article>

<article class="event-card" style="left:799px;top:1200px">
  <div class="poster" role="img" aria-label="Equestrian show poster on gold background" style="background:linear-gradient(#d3a23a,#c8962e)"></div>
  <div class="event-date"><b>20</b><small>FEB</small></div>
</article>

<article class="event-card" style="left:131px;top:1620px">
  <div class="poster" role="img" aria-label="Football club match poster with green and gold crest" style="background:linear-gradient(#151515,#2a2a1e 55%,#3f4a1f 80%,#eeeeee 92%)"></div>
  <div class="event-date"><b>22</b><small>FEB</small></div>
</article>

<article class="event-card" style="left:465px;top:1620px">
  <div class="poster" role="img" aria-label="Family animated musical show poster in bright colours" style="background:linear-gradient(#e85aa8,#4aa0e0 45%,#f4b43a 70%,#1f3f8a)"></div>
  <div class="event-date"><b>26</b><small>FEB</small></div>
</article>

<article class="event-card" style="left:799px;top:1620px">
  <div class="poster" role="img" aria-label="Regional singer concert poster on blue geometric background" style="background:linear-gradient(#f4f6fb,#7fa6e0 55%,#1f4a9a 88%)"></div>
  <div class="event-date"><b>28</b><small>FEB</small></div>
</article>

<footer class="site-footer">
  <div class="social"><span></span><span></span><span></span><span></span><span></span></div>
  <div class="apps"><span><i></i>Appvault</span><span><i></i>Playgrove</span></div>
  <nav class="footer-links"><span>Contact Us</span><span>Privacy</span><span>Accessibility</span><span>Terms of Use</span></nav>
  <div class="footer-rule"></div>
  <div class="copyright">© 2017 Brovlane Pass. All Rights Reserved.</div>
</footer>

</div>
</body>
</html>
```